We need a Word Template for Custom Laboratory Results from an independent laboratory

The test is a novel biomarker for a chronic pain condition called endometriosis. It is expressed as a percentage. We will upload a sample result. We are looking for improved graphic fidelity with more attention to design and spacing. Emphasis should be placed on the overall result, i.e. the patient percentage results. Considerationis going to be given to the most appealing graphic result.

Target Market(s)

Women aged 19-45

Colors
0054AA
0677BA
7BADD7
CADEEF
E8F1F8

```html
<!DOCTYPE html>
<html lang="en">
<head>
<meta charset="utf-8">
<title>Endolyte Micro-RNA Endometriosis Assay – Results</title>
<link href="https://fonts.googleapis.com/css2?family=Montserrat:wght@400;500;600;700&display=swap" rel="stylesheet">
<style>
  :root {
    --blue-deep: #0054AA;
    --blue-main: #0677BA;
    --blue-result: #0a5f8f;
    --blue-mid: #7BADD7;
    --blue-soft: #CADEEF;
    --blue-pale: #E8F1F8;
    --panel-end: #c8dbe3;
    --grey-panel: #e5e5e5;
    --ink: #3c4a57;
    --white: #ffffff;
  }
  * { box-sizing: border-box; margin: 0; padding: 0; }
  html, body { width: 927px; height: 1200px; overflow: hidden; background: var(--white); }
  body { font-family: "Montserrat", sans-serif; }
  .report { position: relative; width: 927px; height: 1200px; }

  .brand { position: absolute; top: 108px; display: flex; align-items: center; gap: 10px;
           font-weight: 600; color: var(--blue-main); font-size: 22px; }
  .brand--clinic { left: 44px; }
  .brand--lab { left: 288px; }
  .brand-dot { width: 34px; height: 34px; border-radius: 50%; background: var(--blue-soft); }

  .assay-title { position: absolute; left: 42px; top: 236px; color: var(--blue-main);
                 font-weight: 700; font-size: 50px; line-height: 56px; letter-spacing: 1px; }

  .results-bar { position: absolute; left: 44px; top: 379px; width: 841px; height: 50px;
                 background: var(--blue-main); color: var(--white); font-weight: 700;
                 font-size: 22px; letter-spacing: 0.5px; padding-left: 35px; line-height: 50px; }

  .patient { position: absolute; left: 78px; top: 470px; color: var(--ink);
             font-weight: 700; font-size: 16px; letter-spacing: 0.5px; }
  .patient-row { height: 38px; line-height: 38px; display: flex; gap: 34px; }

  .result-card { position: absolute; top: 609px; height: 133px;
                 background: linear-gradient(180deg, var(--white) 0%, var(--panel-end) 100%); }
  .result-card--label { left: 45px; width: 463px; display: flex; flex-direction: column;
                        justify-content: center; text-align: center; color: var(--blue-result);
                        font-size: 20px; line-height: 29px; }
  .result-card--label strong { font-weight: 700; }
  .result-card--value { left: 520px; width: 365px; display: flex; align-items: center;
                        justify-content: center; color: var(--blue-result);
                        font-weight: 700; font-size: 86px; }

  .reference { position: absolute; left: 45px; top: 833px; width: 840px; height: 237px;
               background: var(--grey-panel); padding: 22px 0 0 33px; }
  .reference-title { color: var(--blue-main); font-weight: 700; font-size: 22px;
                     letter-spacing: 0.5px; margin-bottom: 10px; }
  .reference-list { list-style: none; color: var(--blue-main); font-size: 20px; line-height: 29.4px; padding-left: 3px; }
</style>
</head>
<body>
<main class="report">
  <div class="brand brand--clinic"><span class="brand-dot"></span>Meridian Fertility</div>
  <div class="brand brand--lab">Veltra</div>

  <h1 class="assay-title">ENDOLYTE MICRO-RNA<br>ENDOMETRIOSIS ASSAY</h1>

  <div class="results-bar">YOUR RESULTS</div>

  <section class="patient">
    <div class="patient-row"><span>[FIRST NAME]</span><span>[LAST NAME]</span></div>
    <div class="patient-row"><span>[OHIP NUMBER (12 CHARACTERS)]</span></div>
    <div class="patient-row"><span>[DOB]</span></div>
  </section>

  <div class="result-card result-card--label">
    <strong>Predicted probability of endometreosis</strong>
    <span>Compared to</span>
    <strong>Surgical Controls (100% Probability)</strong>
  </div>
  <div class="result-card result-card--value">38.7%</div>

  <section class="reference">
    <h2 class="reference-title">REFERENCE RANGE</h2>
    <ol class="reference-list">
      <li>1.&nbsp;&nbsp; 0.0 - 29.9% - low probability of endometriosis</li>
      <li>2.&nbsp; 29.9 - 44.9% - inconclusive</li>
      <li>3.&nbsp; 45.o - 55.0% - intermediate risk of endometriosis</li>
      <li>4.&nbsp; 55.1 - 64.9% - probable endometriosis</li>
      <li>5.&nbsp; 65.0 - 99.9% - highly probable endometriosis</li>
    </ol>
  </section>
</main>
</body>
</html>
```